SkyvornQ Business Cards and Stationary Design

Need a design for our business cards and stationary. I want to carry on the theme of the logo. I want the business cards to have a design on the back. I would like the business cards and the stationary to carry the same theme, design scheme, and branding

Target Market(s)

Airlines and Maintenance Facilities

Industry/Entity Type

Aviation

Contact Information for Business Card

Name
Position Title
Address: 4827 Trellis Hollow Road, Brenmoor Vale, Westmark, 34951
Office Number
Mobile Number
Email
Website

Font styles to use
Serif
Sans Serif

Colors

Designer to choose colors to be used in the design.

```html
<!DOCTYPE html>
<html lang="en">
<head>
<meta charset="utf-8">
<title>SkyvornQ Business Card</title>
<link rel="stylesheet" href="https://fonts.googleapis.com/css2?family=Roboto:wght@300;400;500;700&display=swap">
<style>
  :root {
    --page-bg: #e9ebee;
    --card-white: #fbfbfc;
    --navy: #14306b;
    --deep-blue: #0b3f8c;
    --bright-blue: #1d8fd9;
    --sky-blue: #2aa7e8;
    --text-grey: #3c4350;
    --rule-grey: #9aa0a8;
  }
  * { margin: 0; padding: 0; box-sizing: border-box; }
  html, body { width: 1200px; height: 911px; overflow: hidden; }
  body {
    background: var(--page-bg);
    font-family: "Roboto", Arial, sans-serif;
    position: relative;
  }
  .card {
    position: absolute;
    left: 220px;
    width: 760px;
    height: 420px;
    border-radius: 22px;
    overflow: hidden;
    box-shadow: 0 6px 18px rgba(20, 40, 80, 0.18);
  }
  .card-front { top: 30px; background: var(--card-white); }
  .card-back {
    top: 470px;
    background: radial-gradient(ellipse at 62% 45%, var(--sky-blue) 0%, var(--bright-blue) 22%, var(--deep-blue) 70%, #082f6e 100%);
  }

  .brand-name {
    font-weight: 700;
    letter-spacing: 9px;
    text-transform: uppercase;
    white-space: nowrap;
  }
  .front-brand {
    position: absolute;
    left: 60px;
    top: 140px;
    display: flex;
    align-items: center;
    gap: 16px;
  }
  .brand-dot {
    width: 30px; height: 30px;
    border-radius: 50%;
    background: var(--bright-blue);
  }
  .front-brand .brand-name { font-size: 44px; color: var(--navy); }

  .holder {
    position: absolute;
    right: 50px;
    top: 44px;
    text-align: right;
    width: 380px;
  }
  .holder-name { font-size: 26px; font-weight: 500; color: var(--navy); letter-spacing: 0.5px; }
  .holder-title { font-size: 17px; color: var(--sky-blue); margin-top: 2px; }
  .holder-rule { height: 1px; background: var(--rule-grey); margin-top: 10px; }
  .address {
    position: absolute;
    right: 50px;
    top: 150px;
    text-align: right;
    font-size: 16px;
    line-height: 1.5;
    color: var(--text-grey);
  }

  .contacts {
    position: absolute;
    left: 60px;
    top: 256px;
    border-top: 1px solid var(--rule-grey);
    padding-top: 12px;
    width: 260px;
    list-style: none;
    font-size: 16px;
    color: var(--text-grey);
    line-height: 1.6;
  }
  .contacts li { display: flex; align-items: center; gap: 10px; }
  .contacts svg { width: 14px; height: 14px; fill: var(--navy); flex: none; }

  .edge-band { position: absolute; left: 0; bottom: 0; width: 760px; height: 70px; }
  .website {
    position: absolute;
    right: 50px;
    bottom: 16px;
    font-size: 16px;
    color: #ffffff;
    letter-spacing: 3px;
  }

  .back-brand { position: absolute; left: 50px; top: 40px; }
  .back-brand .brand-name { font-size: 40px; color: #ffffff; }
  .back-url {
    font-size: 15px;
    color: #ffffff;
    letter-spacing: 6px;
    margin-top: 6px;
    font-weight: 300;
  }
</style>
</head>
<body>

<section class="card card-front">
  <div class="front-brand">
    <span class="brand-dot"></span>
    <span class="brand-name">SkyvornQ</span>
  </div>

  <div class="holder">
    <p class="holder-name">DANA WHITFIELD</p>
    <p class="holder-title">CEO/FOUNDER</p>
    <div class="holder-rule"></div>
  </div>

  <p class="address">4827 Trellis Hollow Road<br>Brenmoor Vale, Westmark, 34951</p>

  <ul class="contacts">
    <li>
      <svg viewBox="0 0 16 16"><path d="M3.6 1.2l2.3 2.6-1.3 1.9c.9 2 2.5 3.7 4.6 4.6l1.9-1.3 2.6 2.3-1.2 2.4C7 13.4 2.6 9 1.2 3.8z"/></svg>
      <span>555 214 7093</span>
    </li>
    <li>
      <svg viewBox="0 0 16 16"><path d="M4 1h8v14H4zM5.5 2.5v9h5v-9z"/></svg>
      <span>555 386 1420</span>
    </li>
    <li>
      <svg viewBox="0 0 16 16"><path d="M1 3h14v10H1zM2.5 4.5v.4L8 8.6l5.5-3.7v-.4zM2.5 6.7v4.8h11V6.7L8 10.4z"/></svg>
      <span>info@skyvornq.com</span>
    </li>
  </ul>

  <svg class="edge-band" viewBox="0 0 760 70" preserveAspectRatio="none" aria-hidden="true">
    <defs>
      <linearGradient id="bandFill" x1="0" y1="0" x2="1" y2="0">
        <stop offset="0" stop-color="#14306b"/>
        <stop offset="0.6" stop-color="#0b3f8c"/>
        <stop offset="1" stop-color="#1d8fd9"/>
      </linearGradient>
    </defs>
    <path d="M0 56 H430 C452 56 458 14 482 14 H760 V70 H0 Z" fill="url(#bandFill)"/>
    <path d="M0 52 H428 C450 52 456 10 480 10 H760 V14 H482 C458 14 452 56 430 56 H0 Z" fill="#2aa7e8"/>
  </svg>
  <p class="website">www.skyvornq.com</p>
</section>

<section class="card card-back">
  <div class="back-brand">
    <p class="brand-name">SkyvornQ</p>
    <p class="back-url">skyvornq.com</p>
  </div>
</section>

</body>
</html>
```